Professional Photography Business cards

I need business cards that include my logo which I have uploaded. I run a photography business. I am open to ideas but I would like one side to have my logo and the other side to have my contact info. I don't have a website made but I do own a website domain. I have uploaded 2 different logo color schemes. My business colors are Blue, black , and white.

Business Name
Business Phone Number
Business Email
Business Website address
Instagram

Industry/Entity Type

Professional Photography

Contact Information for Business Card

Phone Number: 916-384-7702 email: info@tlane-studio.example Instagram: @t.lanestudio website doman- www.tlane-studio.example

Requirements
Must have
• I like the idea of a business card with a full black background front and back of card. My colors must include royal blue, black, and white

```html
<!DOCTYPE html>
<html lang="en">
<head>
<meta charset="utf-8">
<title>T. Lane Studio — Business Cards</title>
<link rel="stylesheet" href="https://fonts.googleapis.com/css2?family=Montserrat:wght@600;700&family=Roboto:wght@400;500&display=swap">
<style>
  :root {
    --backdrop: #1c1d1f;
    --card-top: #0d1112;
    --card-bottom: #040506;
    --white: #f2f2f2;
    --soft-white: #d9d9d9;
    --royal-blue: #4a4fc4;
    --divider: #6a6d72;
  }
  * { box-sizing: border-box; margin: 0; padding: 0; }
  html, body {
    width: 1200px; height: 929px; overflow: hidden;
    background: var(--backdrop);
  }
  .canvas {
    position: relative; width: 1200px; height: 929px;
  }
  .card {
    position: absolute; left: 310px;
    width: 580px; height: 331px;
    border-radius: 16px;
    background: linear-gradient(160deg, var(--card-top) 0%, var(--card-bottom) 100%);
    box-shadow: 0 18px 40px rgba(0,0,0,0.55);
    overflow: hidden;
  }
  .card--front { top: 108px; }
  .card--back { top: 490px; }

  .brand {
    position: absolute; display: flex; align-items: center; gap: 14px;
    font-family: "Montserrat", sans-serif; font-weight: 600;
    letter-spacing: 0.5px; white-space: nowrap;
  }
  .brand__dot {
    border-radius: 50%; border: 3px solid currentColor; flex: none;
  }
  .card--front .brand {
    left: 50%; top: 50%; transform: translate(-50%, -50%);
    color: var(--white); font-size: 40px;
  }
  .card--front .brand__dot { width: 44px; height: 44px; }

  .card--back .brand {
    left: 44px; top: 208px; color: var(--royal-blue); font-size: 26px; gap: 10px;
  }
  .card--back .brand__dot { width: 30px; height: 30px; border-width: 2px; }

  .divider {
    position: absolute; left: 292px; top: 70px; width: 1px; height: 200px;
    background: linear-gradient(180deg, transparent, var(--divider) 30%, var(--divider) 70%, transparent);
  }
  .contact {
    position: absolute; left: 318px; top: 72px;
  }
  .contact__name {
    font-family: "Montserrat", sans-serif; font-weight: 700;
    font-size: 27px; color: var(--soft-white); line-height: 1.1;
  }
  .contact__title {
    font-family: "Montserrat", sans-serif; font-weight: 600;
    font-size: 19px; color: var(--royal-blue); margin-top: 4px;
  }
  .contact__list {
    list-style: none; margin-top: 22px;
    font-family: "Roboto", sans-serif; font-size: 15.5px; color: var(--white);
  }
  .contact__item {
    display: flex; align-items: center; gap: 9px; height: 24px;
  }
  .contact__icon { width: 16px; height: 16px; flex: none; }
</style>
</head>
<body>
<main class="canvas">
  <section class="card card--front" aria-label="Card front">
    <div class="brand"><span class="brand__dot"></span>T. Lane Studio</div>
  </section>

  <section class="card card--back" aria-label="Card back">
    <div class="brand"><span class="brand__dot"></span>T. Lane Studio</div>
    <div class="divider"></div>
    <div class="contact">
      <h1 class="contact__name">Tessa Lane</h1>
      <p class="contact__title">CPA, CGA</p>
      <ul class="contact__list">
        <li class="contact__item">
          <svg class="contact__icon" viewBox="0 0 16 16" aria-hidden="true"><path fill="#4a4fc4" d="M3.5 1.5l2.5 0 1 3.5-1.6 1.2a8 8 0 0 0 4.4 4.4L11 9l3.5 1v2.5c0 1-1 2-2 2A11 11 0 0 1 1.5 3.5c0-1 1-2 2-2z"/></svg>
          916-384-7702
        </li>
        <li class="contact__item">
          <svg class="contact__icon" viewBox="0 0 16 16" aria-hidden="true"><rect x="1" y="3" width="14" height="10" rx="1" fill="#4a4fc4"/><path d="M1.5 3.8L8 9l6.5-5.2" fill="none" stroke="#040506" stroke-width="1.3"/></svg>
          info@tlane-studio.example
        </li>
        <li class="contact__item">
          <svg class="contact__icon" viewBox="0 0 16 16" aria-hidden="true"><circle cx="8" cy="8" r="7" fill="#4a4fc4"/><path d="M1 8h14M8 1c-3 3.5-3 10.5 0 14M8 1c3 3.5 3 10.5 0 14" fill="none" stroke="#040506" stroke-width="1"/></svg>
          www.tlane-studio.example
        </li>
        <li class="contact__item">
          <svg class="contact__icon" viewBox="0 0 16 16" aria-hidden="true"><rect x="1" y="1" width="14" height="14" rx="2" fill="#4a4fc4"/></svg>
          @t.lanestudio
        </li>
      </ul>
    </div>
  </section>
</main>
</body>
</html>
```